Looking for a modern, Professional business card design

We have a simple business card, but are looking for a more modern, professional look. A sample of the basic card is attached as well as the logo. We would also like to add that we offer:
Struggling with your finances?
- Learn to become debt free
- Discover the power of cash
- Control your money instead of it controlling you
Let us help you achieve a new level of financial freedom!
Also, we would like to have a "SPECIAL OFFER!: FREE 30 minute consultation"
Financial Planning

```html
<!DOCTYPE html>
<html lang="en">
<head>
<meta charset="utf-8">
<title>Harbor Financial Coaching – Business Card</title>
<link rel="stylesheet" href="https://fonts.googleapis.com/css2?family=Lato:ital,wght@0,400;0,700;1,400;1,700&display=swap">
<style>
  :root {
    --stage: #000000;
    --card-light: #f2f2f2;
    --ink: #1e1e1e;
    --green: #4f9a2a;
    --green-rule: #7cc043;
    --green-top: #8cc63f;
    --green-bottom: #3f9a35;
    --white: #ffffff;
  }
  * { margin: 0; padding: 0; box-sizing: border-box; }
  html, body { width: 1200px; height: 900px; overflow: hidden; background: var(--stage); }
  body { position: relative; font-family: "Lato", Arial, sans-serif; color: var(--ink); }

  .card { position: absolute; top: 200px; width: 310px; height: 502px; }

  .card-front {
    left: 265px;
    background: var(--card-light);
    border-radius: 66px 0 66px 0;
    text-align: center;
    padding-top: 37px;
  }
  .coach-name { font-size: 18.5px; font-weight: 700; color: var(--green); line-height: 1; }
  .coach-role { font-size: 14px; margin-top: 9px; }
  .rule {
    width: 196px; margin: 0 auto;
    border-top: 1px dashed var(--green-rule);
  }
  .rule-1 { margin-top: 13px; }
  .contact { font-size: 14px; line-height: 19.5px; margin-top: 15px; }
  .rule-2 { margin-top: 24px; }
  .headline { font-size: 15px; font-weight: 700; color: var(--green); margin-top: 20px; letter-spacing: .1px; }
  .benefits { list-style: none; font-size: 14px; line-height: 21px; margin-top: 10px; }
  .rule-3 { margin-top: 15px; }
  .promise { font-size: 13.5px; font-weight: 700; font-style: italic; line-height: 20.5px; margin-top: 9px; }
  .rule-4 { margin-top: 7px; }
  .offer-title { font-size: 14.5px; font-weight: 400; margin-top: 22px; }
  .offer-detail { font-size: 13.5px; font-weight: 700; font-style: italic; margin-top: 4px; }

  .card-back {
    left: 641px;
    border-radius: 0 66px 0 66px;
    overflow: hidden;
    background: linear-gradient(180deg, var(--green-top) 0%, #6db53c 45%, var(--green-bottom) 100%);
  }
  .brand-pattern {
    position: absolute; inset: 0;
    background: radial-gradient(ellipse at 50% 40%, rgba(255,255,255,.10), rgba(0,0,0,.05));
  }
  .brand {
    position: absolute; left: 24px; right: 24px; top: 384px;
    display: flex; align-items: center; gap: 10px;
  }
  .brand-dot { width: 28px; height: 28px; border-radius: 50%; background: var(--white); flex: none; }
  .brand-name {
    font-size: 17px; font-weight: 700; color: var(--white);
    line-height: 1.15; letter-spacing: .4px; white-space: nowrap;
  }
</style>
</head>
<body>
  <section class="card card-front">
    <h1 class="coach-name">Daniel R. Hale</h1>
    <p class="coach-role">Personal Financial Coach</p>
    <div class="rule rule-1"></div>
    <p class="contact">
      (205) 555-0182<br>
      daniel@steadymoneypath.com<br>
      www.steadymoneypath.com
    </p>
    <div class="rule rule-2"></div>
    <h2 class="headline">STRUGGLING WITH YOUR FINANCES?</h2>
    <ul class="benefits">
      <li>Learn to become debt free</li>
      <li>Discover the power of cash</li>
      <li>Control your money instead of it<br>controlling you</li>
    </ul>
    <div class="rule rule-3"></div>
    <p class="promise">Let us help you achieve a<br>new level of financial freedom!</p>
    <div class="rule rule-4"></div>
    <p class="offer-title">SPECIAL OFFER!</p>
    <p class="offer-detail">FREE 30 minute consultation</p>
  </section>

  <section class="card card-back">
    <div class="brand-pattern" role="img" aria-label="Repeating faint brand-mark pattern on green background"></div>
    <div class="brand">
      <span class="brand-dot"></span>
      <span class="brand-name">HARBOR<br>FINANCIAL COACHING</span>
    </div>
  </section>
</body>
</html>
```